KRL Stationery Design Project

Dear Designers,
We need a new stationery design for company to match our new logo.
Designers should provide a design for the following:
1. Business Card: 3.5x2 Inches.
2. Letterhead: A4 size.
3. Envelops: 25x35.5 Cm.
You can keep the Arabic name at the bottom of the logo Or you can use the separate attached Arabic Name.
Please refer to the attached logo guide for design information.
Sample Business Card information:
Name: Tarek Sowan
Position: Operation Manager
Tel: +966 920007164 Ex. 500
Fax: +966 (3)8842617
Mob: +966 (5)00263817
email: tarek@krl-example.com.sa
URL: www.krl-example.com.sa
Address:
Nakheel Heights, Suite 718
Zayed bin Omar Str.
Khobar, 31847
Saudi Arabia
Updates
Dear All,
Please note, we had uploaded our logo along with Arabic writing in Adobe illustrator format (.ai).
Regards,
Karim
Dear All,
A sample data for the business card had been added as per your request.
Regards,
Karim

```html
<!DOCTYPE html>
<html lang="en">
<head>
<meta charset="utf-8">
<title>KRL Business Card</title>
<link rel="stylesheet" href="https://fonts.googleapis.com/css2?family=Ubuntu:wght@400;500;700&display=swap">
<style>
  :root {
    --navy: #0d2d56;
    --white: #ffffff;
    --rule-grey: #9a9ca0;
    --text-grey: #5b5e63;
    --backdrop: #e4e2de;
  }
  * { box-sizing: border-box; margin: 0; padding: 0; }
  html, body {
    width: 1200px; height: 472px; overflow: hidden;
    background: var(--backdrop);
    font-family: "Ubuntu", sans-serif;
  }
  .stage { position: relative; width: 1200px; height: 472px; }

  .card {
    position: absolute; top: 83px;
    width: 525px; height: 300px;
    border-radius: 14px; overflow: hidden;
  }
  .card-front { left: 53px; background: var(--white); }
  .card-back { left: 610px; background: var(--navy); }

  /* front */
  .brand-front {
    position: absolute; left: 50px; top: 48px;
    display: flex; align-items: center; gap: 16px;
  }
  .brand-dot {
    width: 34px; height: 34px; border-radius: 50%;
  }
  .brand-front .brand-dot { background: var(--navy); }
  .brand-name {
    font-weight: 700; font-size: 64px; letter-spacing: 2px; line-height: 1;
  }
  .brand-front .brand-name { color: var(--navy); }

  .holder {
    position: absolute; left: 49px; top: 177px;
    color: var(--navy); font-size: 16px; font-weight: 700;
  }
  .holder .role { font-size: 13px; font-weight: 400; color: var(--text-grey); }

  .rule { position: absolute; left: 0; right: 0; top: 204px; height: 3px; background: var(--rule-grey); }
  .contact-band {
    position: absolute; left: 0; right: 0; top: 209px; bottom: 0;
    background: var(--navy); color: var(--white);
    display: flex; align-items: center; padding-left: 40px;
    font-size: 14px; line-height: 17px;
  }
  .contact-col { padding: 0 12px; }
  .contact-col + .contact-col { border-left: 1px solid rgba(255,255,255,.75); }
  .contact-col.address { text-align: right; padding-left: 0; }
  .contact-line { display: flex; align-items: center; gap: 6px; white-space: nowrap; }
  .contact-line svg { width: 11px; height: 11px; flex: none; }

  /* back */
  .brand-back {
    position: absolute; left: 0; right: 0; top: 92px;
    display: flex; justify-content: center; align-items: center; gap: 18px;
  }
  .brand-back .brand-dot { background: var(--white); }
  .brand-back .brand-name { color: var(--white); }
  .back-web {
    position: absolute; left: 0; right: 0; top: 230px;
    display: flex; justify-content: center; align-items: center; gap: 6px;
    color: var(--white); font-size: 13px;
  }
  .back-web svg { width: 11px; height: 11px; }
</style>
</head>
<body>
<div class="stage">

  <section class="card card-front">
    <div class="brand-front">
      <span class="brand-dot"></span>
      <span class="brand-name">KRL</span>
    </div>

    <p class="holder">YOUR NAME, <span class="role">Title</span></p>

    <div class="rule"></div>
    <div class="contact-band">
      <div class="contact-col address">
        <div>Street Name, City, State</div>
        <div>City Zip Code 000 000</div>
      </div>
      <div class="contact-col phones">
        <div class="contact-line">
          <svg viewBox="0 0 12 12" aria-hidden="true"><path fill="#fff" d="M2.5 1l2 2.2-1 1.2c.7 1.5 1.8 2.6 3.2 3.2l1.2-1L10 8.6 9 10.7C5 10.5 1.5 7 1.3 3z"/></svg>
          <span>123-456-7890</span>
        </div>
        <div class="contact-line">
          <svg viewBox="0 0 12 12" aria-hidden="true"><path fill="#fff" d="M2.5 3.5L3.5 1.5h5l1 2 1 .5v4H9v1.5H7.5V8h-3v1.5H3V8H1.5V4z"/></svg>
          <span>123-456-7890</span>
        </div>
      </div>
      <div class="contact-col online">
        <div class="contact-line">
          <svg viewBox="0 0 12 12" aria-hidden="true"><rect x="1" y="2.5" width="10" height="7" rx="1" fill="#fff"/><path d="M1.5 3l4.5 3.5L10.5 3" stroke="#0d2d56" fill="none"/></svg>
          <span>info@mail-example.com</span>
        </div>
        <div class="contact-line">
          <svg viewBox="0 0 12 12" aria-hidden="true"><circle cx="6" cy="6" r="5" fill="#fff"/><path d="M1 6h10M6 1v10M2 3.5h8M2 8.5h8" stroke="#0d2d56" stroke-width=".7"/></svg>
          <span>www.website.com</span>
        </div>
      </div>
    </div>
  </section>

  <section class="card card-back">
    <div class="brand-back">
      <span class="brand-dot"></span>
      <span class="brand-name">KRL</span>
    </div>
    <div class="back-web">
      <svg viewBox="0 0 12 12" aria-hidden="true"><circle cx="6" cy="6" r="5" fill="#fff"/><path d="M1 6h10M6 1v10M2 3.5h8M2 8.5h8" stroke="#0d2d56" stroke-width=".7"/></svg>
      <span>www.website.com</span>
    </div>
  </section>

</div>
</body>
</html>
```